KLT - FlowFest 2022 Tradfe show 10'Wx8' display

My company Crafted Units & Machinery, inc. ( K.L.T) has a display booth at the 2022 Virginia flow fest water wastewater trade show next month and would like new backdrop art for our 10'x8' banner stand. our website is
www.klt-halvorn.example and our company line card is attached to give an idea of what we do. We want the main takeaway from the artwork to let customers know we offer Pumps, Blowers, Motors , Drives & Repair Services for the Municipal water & wastewater industry. Needs this in a high res pdf.

```html
<!DOCTYPE html>
<html lang="en">
<head>
<meta charset="UTF-8">
<title>KLT – FlowFest 2022 Backdrop</title>
<link href="https://fonts.googleapis.com/css2?family=Montserrat:wght@300;400;700;800;900&display=swap" rel="stylesheet">
<style>
  :root {
    --page-bg: #e8e8e8;
    --brand-blue: #1560ad;
    --deep-blue: #0d4a8c;
    --mid-blue: #2a73bb;
    --brand-orange: #ea6c16;
    --white: #ffffff;
    --ink: #1b1b1b;
    --icon-grey: #7b7f86;
    --icon-grey-dark: #565a61;
    --photo-olive: #6f7a55;
    --photo-tan: #c9a15a;
  }
  * { box-sizing: border-box; margin: 0; padding: 0; }
  html, body {
    width: 800px; height: 1200px; overflow: hidden;
    background: var(--page-bg);
    font-family: "Montserrat", sans-serif;
  }
  .banner {
    position: absolute; left: 20px; top: 296px;
    width: 760px; height: 607px;
    overflow: hidden;
    box-shadow: 0 4px 14px rgba(0,0,0,0.18);
    background: var(--white);
  }
  .banner-backdrop {
    position: absolute; left: 0; top: 0; width: 760px; height: 432px;
    background:
      radial-gradient(ellipse at 75% 70%, rgba(60,120,190,0.55), transparent 60%),
      linear-gradient(100deg, var(--brand-blue) 0%, var(--mid-blue) 45%, var(--deep-blue) 100%);
  }
  .company-name {
    position: absolute; left: 31px; top: 44px; z-index: 2;
    font-weight: 900; font-size: 58px; line-height: 1;
    color: var(--white); letter-spacing: 1px;
  }
  .headline {
    position: absolute; left: 28px; top: 126px; width: 380px; z-index: 2;
    color: var(--white);
  }
  .headline-year { font-weight: 300; font-size: 66px; line-height: 66px; letter-spacing: -1px; }
  .headline-event { font-weight: 300; font-size: 43px; line-height: 50px; letter-spacing: -0.5px; white-space: nowrap; }
  .headline-strong {
    font-weight: 800; font-size: 48px; line-height: 60px; letter-spacing: -1px;
    white-space: nowrap;
  }
  .headline-rule {
    position: absolute; left: 29px; top: 380px; width: 369px; height: 1px; z-index: 2;
    background: rgba(255,255,255,0.55);
  }
  .headline-rule-accent {
    position: absolute; left: 61px; top: 377px; width: 73px; height: 7px; z-index: 2;
    border-radius: 4px; background: var(--white);
  }
  .presenter-photo {
    position: absolute; left: 430px; top: 26px; width: 270px; height: 406px; z-index: 1;
    border-radius: 120px 120px 0 0;
    background: linear-gradient(180deg, var(--photo-olive) 0%, #7d8660 55%, var(--photo-tan) 78%, #8a8a68 100%);
    opacity: 0.9;
  }
  .services-band {
    position: absolute; left: 0; top: 432px; width: 760px; height: 92px; z-index: 2;
    background: var(--brand-orange);
    border-top: 3px solid var(--white);
  }
  .service {
    position: absolute; top: 404px; width: 150px; margin-left: -75px; z-index: 3;
    text-align: center; color: var(--white);
  }
  .service-icon {
    display: block; margin: 0 auto;
    width: 55px; height: 55px; border-radius: 50%;
    background: radial-gradient(circle at 40% 35%, var(--icon-grey), var(--icon-grey-dark));
    border: 2px solid var(--brand-blue);
    box-shadow: 0 0 0 1px var(--white);
  }
  .service-label {
    margin-top: 6px; font-weight: 700; font-size: 17px; line-height: 23px;
    white-space: nowrap;
  }
  .site-footer {
    position: absolute; left: 0; top: 524px; width: 760px; height: 83px;
    background: var(--white);
  }
  .site-url {
    position: absolute; left: 0; top: 22px; width: 760px; text-align: center;
    font-weight: 700; font-size: 18px; letter-spacing: 1.8px; color: var(--ink);
  }
</style>
</head>
<body>
  <main class="banner">
    <div class="banner-backdrop" role="img" aria-label="Blue-tinted photo of an industrial pump room with pipes and machinery"></div>

    <div class="presenter-photo" role="img" aria-label="Photo of a technician in olive coveralls and a yellow tool belt gesturing toward the headline"></div>

    <div class="company-name">KLT</div>

    <div class="headline">
      <div class="headline-year">2022</div>
      <div class="headline-event">VIRGINIA FLOW</div>
      <div class="headline-strong">FEST WATER</div>
      <div class="headline-strong">WASTEWATER</div>
    </div>
    <div class="headline-rule"></div>
    <div class="headline-rule-accent"></div>

    <div class="services-band"></div>

    <div class="service" style="left:70px"><span class="service-icon"></span><div class="service-label">Pumps</div></div>
    <div class="service" style="left:161px"><span class="service-icon"></span><div class="service-label">Blowers</div></div>
    <div class="service" style="left:248px"><span class="service-icon"></span><div class="service-label">Motors</div></div>
    <div class="service" style="left:336px"><span class="service-icon"></span><div class="service-label">Drives</div></div>
    <div class="service" style="left:485px"><span class="service-icon"></span><div class="service-label">Repair Services for<br>the Municipal water</div></div>
    <div class="service" style="left:664px"><span class="service-icon"></span><div class="service-label">Wastewater<br>industry</div></div>

    <footer class="site-footer">
      <div class="site-url">www.klt-halvorn.example</div>
    </footer>
  </main>
</body>
</html>
```